HushHarbors.com

Updated Website Structure for HushHarbor.com
1. Home Page

(Add social media links in footer or sidebar)
Suggested addition:

Stay Connected
Follow Hush Harbor for daily encouragement, calming tools, and community stories.

[Circlebook Icon] [Snapgram Icon] [StreamTube Icon]
@HushHarborOfficial

2. How It Works

(No major change — keep focused on process and trust building)

3. Ebook Store

(Add social links at the bottom of the page)

Want more free content?
Follow us on social media for sneak peeks, affirmations, and updates on new releases!

[Circlebook] [Snapgram] [StreamTube]

4. Certification Page

(Optional social proof addition)

Connect with Certified Hush Harbors
Join our online community and see real stories of growth and courage.

Follow us on social media to see how others are supporting each other:

5. Membership Tiers

(Keep page simple, but can include icons in footer)

6. About Me

Suggested addition:

Let’s Stay Connected
I love hearing from others walking this path.

Circlebook: @HushHarborOfficial

Snapgram: @HushHarborOfficial

StreamTube: Hush Harbor Channel

7. Disclosure Page

(Keep links in footer only for professional feel.)

8. Global Footer (Site-wide)

Every page should include a calming footer with:

Navigation links (Home | About Me | How It Works | Ebook Store | Certification | Membership | Disclosure)

Social media icons

Copyright info

Example footer text:

🌿 Walking with fear, choosing courage, calming the nervous system together.

© 2025 HushHarbor.com | All rights reserved

```html
<!DOCTYPE html>
<html lang="en">
<head>
<meta charset="utf-8">
<title>Hush Harbors — Walking With Fear, Choosing Courage</title>
<link rel="stylesheet" href="https://fonts.googleapis.com/css2?family=Josefin+Sans:wght@300;400;600&family=Poiret+One&display=swap">
<style>
:root{
  --pink:#d9a3d6;
  --pink-soft:#edc5ea;
  --pink-deep:#e2a9de;
  --blush:#f8ebf7;
  --mist:#f6f6f8;
  --plum:#3b0a3a;
  --plum-dark:#2e0a2c;
  --ink:#2a2230;
  --white:#ffffff;
}
*{box-sizing:border-box;margin:0;padding:0}
html,body{width:1200px;height:2839px;overflow:hidden;background:var(--white)}
body{position:relative;font-family:"Josefin Sans",sans-serif;color:var(--ink)}
.abs{position:absolute}
.display{font-family:"Poiret One",sans-serif;color:var(--pink);letter-spacing:1px;text-transform:uppercase}

/* header */
.hero-bg{left:0;top:0;width:1200px;height:480px}
.brand{left:110px;top:22px;display:flex;align-items:center;gap:8px;font-size:17px;font-weight:600;color:var(--plum)}
.brand .dot{width:30px;height:30px;border-radius:50%;background:var(--pink-soft)}
.nav{top:48px;display:flex;font-size:14.5px;text-transform:uppercase;color:var(--ink)}
.nav a{position:absolute;white-space:nowrap;color:inherit;text-decoration:none}
.nav .active{color:var(--pink)}
.search{left:1051px;top:38px;width:36px;height:36px;border-radius:50%;background:var(--pink-soft)}

.hero-title{left:110px;top:140px;font-size:38px;line-height:57px}
.hero-text{left:112px;top:262px;width:460px;font-size:17px;line-height:34px}
.btn{display:flex;align-items:center;height:42px;background:var(--pink-soft);font-size:14.5px;text-transform:uppercase;color:var(--plum);text-decoration:none}
.btn .arrow{width:32px;height:42px;background:var(--pink-deep);display:flex;align-items:center;justify-content:center;margin-right:18px}
.hero-emblem{left:614px;top:105px;width:477px;height:407px;display:flex;align-items:center;justify-content:center}
.hero-emblem .circle{width:400px;height:400px;border-radius:50%;background:radial-gradient(circle,#f0b8c4 0%,#e9c2e6 65%);display:flex;align-items:center;justify-content:center;font-family:"Josefin Sans",sans-serif;font-weight:600;font-size:44px;color:var(--plum)}

/* values */
.section-title{font-size:36px}
.rule{height:3px;background:var(--pink-soft)}
.values-text{left:108px;top:655px;width:440px;font-size:16.5px;line-height:35px}
.card{width:234px;height:191px;background:var(--white);border-radius:12px;box-shadow:0 0 10px rgba(120,60,120,.12);padding:22px 18px 0 20px;overflow:hidden}
.card .icon{width:56px;height:56px;border-radius:50%;background:#f7dff5}
.card h3{margin-top:30px;font-size:17px;font-weight:600;line-height:34px;text-transform:uppercase;color:var(--plum);white-space:nowrap}

/* about */
.about-band{left:0;top:1068px;width:1200px;height:752px;background:var(--blush)}
.about-lead{left:112px;top:1196px;width:500px;font-size:16.5px;line-height:37px;text-transform:uppercase;color:var(--plum)}
.about-text{left:658px;top:1131px;width:440px;font-size:16.5px;line-height:33.3px;color:var(--ink)}
.photo-portrait{left:111px;top:1331px;width:476px;height:299px;border-radius:12px;background:linear-gradient(135deg,#f1ece8,#d9b7a6 50%,#b83a3e)}
.photo-field{left:535px;top:1470px;width:562px;height:275px;background:var(--white);border-radius:14px;padding:7px}
.photo-field div{width:100%;height:100%;border-radius:10px;background:linear-gradient(180deg,#8d8ba4 0%,#797a80 45%,#55603e 100%)}

/* how it works */
.steps-icon{width:84px;height:84px;border-radius:50%;border:1px solid #e3d3e2;background:#fbf1fa}
.step-title{width:360px;text-align:center;font-size:19px;font-weight:600;text-transform:uppercase;color:var(--plum)}
.step-text{width:270px;text-align:center;font-size:16.5px;line-height:33px}

/* footer */
.footer{left:0;top:2397px;width:1200px;height:442px;background:var(--plum-dark);color:var(--white)}
.footer .brand{color:var(--white);font-size:22px;left:112px;top:88px}
.footer .brand .dot{width:44px;height:44px}
.footer-tagline{left:112px;top:234px;width:290px;font-family:"Poiret One",sans-serif;font-size:18px;line-height:37px;text-transform:uppercase}
.footer h4{font-family:"Poiret One",sans-serif;font-weight:400;font-size:25px;text-transform:uppercase}
.footer ul{list-style:none;font-size:14.5px;text-transform:uppercase;line-height:38.6px}
.footer-rule{left:100px;top:375px;width:1000px;height:1px;background:rgba(255,255,255,.15)}
.copyright{left:0;top:400px;width:1200px;text-align:center;font-size:14.5px;text-transform:uppercase}
</style>
</head>
<body>

<!-- hero -->
<svg class="abs hero-bg" viewBox="0 0 1200 480" aria-hidden="true">
  <path d="M0 0H1200V110C1090 90 900 110 780 250C680 380 500 470 300 475C150 478 60 420 0 330Z" fill="var(--mist)"/>
</svg>

<div class="abs brand"><span class="dot"></span>Hush Harbors</div>
<nav class="abs nav">
  <a class="active" style="left:422px">Home</a>
  <a style="left:500px">About Me</a>
  <a style="left:611px">How It Works</a>
  <a style="left:756px">Ebook Store</a>
  <a style="left:893px">Certification</a>
</nav>
<div class="abs search">
  <svg width="36" height="36" viewBox="0 0 36 36" aria-hidden="true"><circle cx="17" cy="17" r="5" fill="none" stroke="#fff" stroke-width="1.8"/><path d="M21 21l4 4" stroke="#fff" stroke-width="1.8"/></svg>
</div>

<h1 class="abs display hero-title">Walking with fear.<br>Choosing courage.</h1>
<p class="abs hero-text">Tools and support to help you calm your nervous system and build resilience.</p>
<a class="abs btn" style="left:112px;top:358px;width:224px">
  <span class="arrow"><svg width="12" height="12" viewBox="0 0 12 12" aria-hidden="true"><path d="M2 10L10 2M4 2h6v6" fill="none" stroke="var(--plum)" stroke-width="1.4"/></svg></span>Join the community
</a>
<div class="abs hero-emblem" role="img" aria-label="Hush Harbors emblem with two companions holding hands">
  <div class="circle">Hush Harbors</div>
</div>

<!-- core values -->
<h2 class="abs display section-title" style="left:110px;top:572px">Our core values</h2>
<div class="abs rule" style="left:111px;top:625px;width:48px"></div>
<p class="abs values-text">We meet every person where they are — with empathy, patience, and understanding. Healing begins when we feel seen, not fixed.</p>

<div class="abs card" style="left:606px;top:579px"><div class="icon" role="img" aria-label="Heart in open hands icon"></div><h3>Compassion<br>before correction</h3></div>
<div class="abs card" style="left:854px;top:579px"><div class="icon" role="img" aria-label="Raised fist icon"></div><h3>Courage over<br>comfort</h3></div>
<div class="abs card" style="left:110px;top:791px"><div class="icon" role="img" aria-label="Gear with tick icon"></div><h3>Simplicity that<br>soothes</h3></div>
<div class="abs card" style="left:358px;top:791px"><div class="icon" role="img" aria-label="Interlocking gears icon"></div><h3>Integrity<br>always</h3></div>
<div class="abs card" style="left:606px;top:791px"><div class="icon" role="img" aria-label="Head with lotus icon"></div><h3>Calm through<br>connection</h3></div>
<div class="abs card" style="left:854px;top:791px"><div class="icon" role="img" aria-label="Figure climbing steps to a flag icon"></div><h3>Growth with<br>grace</h3></div>

<!-- about -->
<div class="abs about-band"></div>
<h2 class="abs display section-title" style="left:112px;top:1129px">About us</h2>
<div class="abs rule" style="left:301px;top:1148px;width:48px"></div>
<p class="abs about-lead">We believe healing is not about eliminating fear –<br>it’s about walking with it courageously,<br>with understanding and support.</p>
<p class="abs about-text">Hush Harbor was created to be a calm companion for anyone learning to regulate their nervous system and build resilience. Through practical tools, supportive community, and gentle education, we help you reconnect with safety, one breath at a time. We believe healing is not about eliminating fear — it’s about walking with it courageously, with understanding and support.</p>
<a class="abs btn" style="left:658px;top:1391px;width:164px">
  <span class="arrow"><svg width="12" height="12" viewBox="0 0 12 12" aria-hidden="true"><path d="M2 10L10 2M4 2h6v6" fill="none" stroke="var(--plum)" stroke-width="1.4"/></svg></span>Learn more
</a>
<div class="abs photo-portrait" role="img" aria-label="Portrait photo of the founder in red glasses"></div>
<div class="abs photo-field"><div role="img" aria-label="Photo of two people meditating in a misty meadow"></div></div>

<!-- how it works -->
<h2 class="abs display section-title" style="left:0;top:1898px;width:1200px;text-align:center">How it works</h2>
<div class="abs rule" style="left:577px;top:1955px;width:46px"></div>

<div class="abs steps-icon" style="left:198px;top:2002px" role="img" aria-label="Open book with lightbulb icon"></div>
<div class="abs steps-icon" style="left:560px;top:2002px" role="img" aria-label="Hand with lightbulb and gear icon"></div>
<div class="abs steps-icon" style="left:919px;top:2002px" role="img" aria-label="Connected people icon"></div>

<h3 class="abs step-title" style="left:60px;top:2125px">Learn</h3>
<h3 class="abs step-title" style="left:422px;top:2125px">Practice</h3>
<h3 class="abs step-title" style="left:781px;top:2125px">Connect</h3>
<p class="abs step-text" style="left:105px;top:2163px">Understand what’s happening in<br>your body and mind.</p>
<p class="abs step-text" style="left:467px;top:2163px">Apply calming tools and grounding<br>techniques that work.</p>
<p class="abs step-text" style="left:806px;top:2163px;width:280px">Join a community of others who<br>get it — no judgment, just support.</p>
<a class="abs btn" style="left:496px;top:2268px;width:206px">
  <span class="arrow"><svg width="12" height="12" viewBox="0 0 12 12" aria-hidden="true"><path d="M2 10L10 2M4 2h6v6" fill="none" stroke="var(--plum)" stroke-width="1.4"/></svg></span>See how it works
</a>

<!-- footer -->
<footer class="abs footer">
  <div class="abs brand"><span class="dot"></span>Hush Harbors</div>
  <p class="abs footer-tagline">Walking with fear, choosing courage, calming the nervous system together.</p>
  <h4 class="abs" style="left:497px;top:60px">Quick links</h4>
  <ul class="abs" style="left:497px;top:116px"><li>Home</li><li>About Me</li><li>How It Works</li><li>Ebook Store</li></ul>
  <ul class="abs" style="left:676px;top:116px"><li>Certification</li><li>Membership</li><li>Disclosure</li></ul>
  <h4 class="abs" style="left:899px;top:60px">Stay connected</h4>
  <ul class="abs" style="left:899px;top:116px"><li>Circlebook</li><li>Snapgram</li><li>StreamTube</li></ul>
  <div class="abs footer-rule"></div>
  <p class="abs copyright">© 2025 HushHarbor.com | All rights reserved</p>
</footer>

</body>
</html>
```